Residential Remodeling Contractor needs updated business card

I need a new design for my business card.
Name of the company is Ridgefell Construction. I need a card that commands presence, strength, integrity. I have been in business for 28 years. I am a Residential Remodeling Contractor that covers all aspects of a residential remodel and build.

```html
<!DOCTYPE html>
<html lang="en">
<head>
<meta charset="utf-8">
<title>Ridgefell Construction — Business Card</title>
<link rel="stylesheet" href="https://fonts.googleapis.com/css2?family=Arimo:wght@400;700&display=swap">
<style>
  :root {
    --backdrop: #2b2a2e;
    --card-blue: #1c3f80;
    --card-blue-deep: #183873;
    --emboss-blue: #2a4c8c;
    --ink-white: #ffffff;
    --rule-white: rgba(255, 255, 255, 0.85);
  }
  * { box-sizing: border-box; margin: 0; padding: 0; }
  html, body {
    width: 1200px;
    height: 912px;
    overflow: hidden;
    background: var(--backdrop);
    font-family: "Arimo", Arial, sans-serif;
  }
  .canvas {
    position: relative;
    width: 1200px;
    height: 912px;
    display: flex;
    flex-direction: column;
    align-items: center;
    justify-content: center;
    gap: 32px;
  }
  .card {
    position: relative;
    width: 700px;
    height: 400px;
    border-radius: 22px;
    background: var(--card-blue);
    color: var(--ink-white);
    overflow: hidden;
  }
  .card--back {
    background: linear-gradient(120deg, var(--card-blue-deep) 0%, var(--card-blue) 60%, #23478a 100%);
  }

  /* back side */
  .back-wordmark {
    position: absolute;
    inset: 0;
    display: flex;
    align-items: center;
    justify-content: center;
    gap: 18px;
  }
  .back-wordmark__square {
    width: 44px;
    height: 44px;
    background: var(--emboss-blue);
  }
  .back-wordmark__name {
    font-size: 44px;
    font-weight: 700;
    letter-spacing: 3px;
    text-transform: uppercase;
    color: var(--emboss-blue);
  }

  /* front side */
  .brand {
    position: absolute;
    top: 58px;
    right: 56px;
    display: flex;
    align-items: center;
    gap: 12px;
  }
  .brand__square {
    width: 22px;
    height: 22px;
    background: var(--ink-white);
  }
  .brand__name {
    font-size: 26px;
    font-weight: 700;
    letter-spacing: 1.5px;
    text-transform: uppercase;
    color: var(--ink-white);
  }
  .divider {
    position: absolute;
    left: 56px;
    right: 40px;
    top: 244px;
    height: 1px;
    background: var(--rule-white);
  }
  .person {
    position: absolute;
    left: 56px;
    top: 186px;
  }
  .person__name {
    font-size: 28px;
    font-weight: 700;
    letter-spacing: 0.5px;
    text-transform: uppercase;
    line-height: 1;
  }
  .person__title {
    margin-top: 6px;
    font-size: 16px;
    font-weight: 400;
  }
  .contacts {
    position: absolute;
    left: 56px;
    top: 270px;
    list-style: none;
    display: flex;
    flex-direction: column;
    gap: 10px;
  }
  .contacts__item {
    display: flex;
    align-items: center;
    gap: 12px;
    font-size: 16px;
  }
  .contacts__icon {
    width: 16px;
    height: 16px;
    flex: none;
  }
  .address {
    position: absolute;
    right: 56px;
    top: 264px;
    text-align: right;
    font-size: 16px;
    line-height: 1.45;
  }
</style>
</head>
<body>
<main class="canvas">

  <section class="card card--back" aria-label="Card back">
    <div class="back-wordmark">
      <span class="back-wordmark__square"></span>
      <span class="back-wordmark__name">Ridgefell Construction</span>
    </div>
  </section>

  <section class="card card--front" aria-label="Card front">
    <div class="brand">
      <span class="brand__square"></span>
      <span class="brand__name">Ridgefell Construction</span>
    </div>

    <div class="person">
      <h1 class="person__name">Marcus Delaney</h1>
      <p class="person__title">Owner &amp; Manager</p>
    </div>

    <div class="divider"></div>

    <ul class="contacts">
      <li class="contacts__item">
        <svg class="contacts__icon" viewBox="0 0 16 16" aria-hidden="true">
          <path fill="#fff" d="M3.5 1.5l2.3 2.6-1.3 1.8c.9 2 2.6 3.7 4.6 4.6l1.8-1.3 2.6 2.3-1.4 2.3C7.2 13.5 2.5 8.8 1.2 3z"/>
        </svg>
        <span>555 214 7730</span>
      </li>
      <li class="contacts__item">
        <svg class="contacts__icon" viewBox="0 0 16 16" aria-hidden="true">
          <rect x="1" y="3" width="14" height="10" rx="1" fill="#fff"/>
          <path d="M1.5 3.8L8 9l6.5-5.2" fill="none" stroke="#1c3f80" stroke-width="1.3"/>
        </svg>
        <span>info@ridgefellconstruction.com</span>
      </li>
      <li class="contacts__item">
        <svg class="contacts__icon" viewBox="0 0 16 16" aria-hidden="true">
          <circle cx="8" cy="8" r="7" fill="#fff"/>
          <path d="M1 8h14M8 1c2.4 2.2 2.4 11.8 0 14M8 1c-2.4 2.2-2.4 11.8 0 14" fill="none" stroke="#1c3f80" stroke-width="1"/>
        </svg>
        <span>www.ridgefellconstruction.com</span>
      </li>
    </ul>

    <address class="address" style="font-style: normal;">
      P.O. Box&nbsp; Street Name<br>
      Country Name AB, A5B 521
    </address>
  </section>

</main>
</body>
</html>
```